Cognitive therapist.

I am a therapist and my main work is with clients who have depression and anxiety disorders.

I need something reasonably plain. Cognitive therapy is a very pragmatic approach to dealing with problems, so it isn't new agey (no offence to new age therapies at all)
Updates

Hi everyone, I am currently looking at a particular design that I will most likely go with. Cheers, Meg

Industry/Entity Type

Work

Contact Information for Business Card

Meg Tarvish
Cognitive Therapist
BA, PG Dip Mental Health,
PG Dip Cog Beh Therapy
MKTPR

The Quarry Lodge,
Level One
48 Marlow Parade
Cnr Fenwick St & Marlow Parade
P O Box 38 219
WELLINGTON 6143

Phone: 021 574 3082 Email: mtarvish@quellnet.co.nz

www.megtarvish.co.nz

Requirements
Should not have
• No illustration, or colour. not old style fonts.

```html
<!DOCTYPE html>
<html lang="en">
<head>
<meta charset="utf-8">
<title>Cognitive Therapy — Meg Tarvish</title>
<link rel="stylesheet" href="https://fonts.googleapis.com/css2?family=Oswald:wght@400;600&family=Open+Sans:wght@400&display=swap">
<style>
  :root {
    --page: #e9e7e3;
    --card-light: #ffffff;
    --card-shade: #dcdcdc;
    --band: #3a3d40;
    --accent-ink: #4a4d50;
    --ink-dark: #2f2f2f;
    --ink-mid: #3d3d3d;
    --on-band: #ffffff;
  }
  * { box-sizing: border-box; margin: 0; padding: 0; }
  html, body {
    width: 1200px; height: 1019px; overflow: hidden;
    background: var(--page);
  }
  .stage {
    width: 1200px; height: 1019px;
    display: flex; align-items: center; justify-content: center;
  }
  .business-card {
    position: relative;
    width: 840px; height: 480px;
    background: radial-gradient(ellipse at 55% 45%, var(--card-light) 0%, #f3f3f3 45%, var(--card-shade) 100%);
    box-shadow: 0 14px 30px rgba(0,0,0,0.22);
    overflow: hidden;
  }
  .practice-name {
    position: absolute; left: 52px; top: 196px;
    font-family: "Open Sans", sans-serif; font-weight: 400;
    font-size: 42px; color: var(--accent-ink);
    letter-spacing: 0.5px;
  }
  .person {
    position: absolute; right: 56px; top: 178px;
    text-align: right;
  }
  .person-name {
    font-family: "Oswald", sans-serif; font-weight: 600;
    font-size: 46px; line-height: 1; color: var(--ink-dark);
    letter-spacing: 1px;
  }
  .person-role {
    margin-top: 8px;
    font-family: "Oswald", sans-serif; font-weight: 400;
    font-size: 17px; color: var(--ink-mid);
    letter-spacing: 2.5px;
  }
  .contact-band {
    position: absolute; left: 0; right: 0; top: 300px; bottom: 0;
    background: var(--band);
    color: var(--on-band);
  }
  .band-rule {
    position: absolute; left: 0; right: 0; top: 26px; height: 34px;
  }
  .contact-group {
    position: absolute; top: 26px;
  }
  .contact-label {
    display: inline-block;
    font-family: "Oswald", sans-serif; font-weight: 600;
    font-size: 30px; line-height: 34px;
    letter-spacing: 1.5px;
    padding: 0 14px;
    background: var(--band);
  }
  .contact-lines {
    margin-top: 16px; padding-left: 14px;
    font-family: "Open Sans", sans-serif; font-size: 15px; line-height: 25px;
    white-space: nowrap;
  }
  .group-address { left: 44px; }
  .group-phone { left: 322px; }
  .group-email { left: 588px; }
</style>
</head>
<body>
<main class="stage">
  <article class="business-card">
    <h1 class="practice-name">Cognitive Therapy</h1>

    <div class="person">
      <p class="person-name">MEG TARVISH</p>
      <p class="person-role">COGNITIVE THERAPIST</p>
    </div>

    <section class="contact-band">
      <svg class="band-rule" width="840" height="34" viewBox="0 0 840 34" aria-hidden="true">
        <rect x="0" y="14" width="840" height="7" fill="#ffffff"/>
      </svg>

      <div class="contact-group group-address">
        <span class="contact-label">ADDRESS</span>
        <p class="contact-lines">The Quarry Lodge, Level One<br>48 Marlow Parade, Wellington</p>
      </div>

      <div class="contact-group group-phone">
        <span class="contact-label">PHONE</span>
        <p class="contact-lines">021 574 3082<br>P O Box 38 219</p>
      </div>

      <div class="contact-group group-email">
        <span class="contact-label">EMAIL</span>
        <p class="contact-lines">mtarvish@quellnet.co.nz<br>www.megtarvish.co.nz</p>
      </div>
    </section>
  </article>
</main>
</body>
</html>
```